Tall Fern Roofing Business Card

Need a business card with the logo that was designed here

Contact Information for Business Card

Name, Title, Phone, Email, Website, Company name

```html
<!DOCTYPE html>
<html lang="en">
<head>
<meta charset="utf-8">
<title>Tall Fern Roofing – Business Card</title>
<link href="https://fonts.googleapis.com/css2?family=Montserrat:wght@400;500;700&display=swap" rel="stylesheet">
<style>
  :root {
    --page-bg: #eef0f1;
    --card-front: #807f80;
    --front-mark: #d4d4d6;
    --card-white: #ffffff;
    --brand-blue: #3f72ba;
    --brand-grey: #8a8a8c;
    --text-grey: #6d6d70;
    --shadow: rgba(0, 0, 0, 0.12);
  }
  * { box-sizing: border-box; margin: 0; padding: 0; }
  html, body {
    width: 1200px;
    height: 900px;
    overflow: hidden;
    background: var(--page-bg);
    font-family: "Montserrat", sans-serif;
  }
  .sheet {
    width: 1200px;
    height: 900px;
    display: flex;
    flex-direction: column;
    align-items: center;
    justify-content: center;
    gap: 56px;
  }
  .card {
    position: relative;
    width: 640px;
    height: 366px;
    overflow: hidden;
    box-shadow: 0 10px 28px var(--shadow);
  }

  /* Front */
  .card-front {
    background: var(--card-front);
    display: flex;
    align-items: center;
    justify-content: center;
  }
  .front-brand {
    display: flex;
    align-items: center;
    gap: 14px;
    color: var(--front-mark);
    font-weight: 700;
    font-size: 34px;
    letter-spacing: 1px;
  }
  .front-brand .brand-square {
    width: 22px;
    height: 22px;
    background: var(--front-mark);
  }

  /* Back */
  .card-back { background: var(--card-white); }
  .back-wave {
    position: absolute;
    inset: 0;
    width: 100%;
    height: 100%;
  }
  .back-brand {
    position: absolute;
    left: 40px;
    top: 138px;
    width: 230px;
    display: flex;
    align-items: center;
    gap: 10px;
    color: var(--brand-blue);
    font-weight: 700;
    font-size: 21px;
    line-height: 1.2;
  }
  .back-brand .brand-square {
    flex: none;
    width: 16px;
    height: 16px;
    background: var(--brand-blue);
  }
  .divider {
    position: absolute;
    left: 292px;
    top: 92px;
    width: 1px;
    height: 150px;
    background: var(--brand-blue);
  }
  .contact {
    position: absolute;
    left: 318px;
    top: 46px;
    color: var(--text-grey);
  }
  .contact-name {
    color: var(--brand-blue);
    font-weight: 700;
    font-size: 24px;
    letter-spacing: 1px;
    text-transform: uppercase;
  }
  .contact-title {
    font-size: 14px;
    margin-top: 2px;
  }
  .contact-list {
    list-style: none;
    margin-top: 16px;
  }
  .contact-list li {
    display: flex;
    align-items: center;
    gap: 8px;
    font-size: 14px;
    line-height: 24px;
  }
  .contact-list svg { width: 12px; height: 12px; flex: none; }
  .contact-address {
    margin-top: 12px;
    margin-left: 20px;
    font-size: 14px;
    line-height: 20px;
  }
</style>
</head>
<body>
<main class="sheet">

  <section class="card card-front" aria-label="Card front">
    <div class="front-brand">
      <span class="brand-square"></span>
      <span class="brand-name">Tall Fern Roofing</span>
    </div>
  </section>

  <section class="card card-back" aria-label="Card back">
    <svg class="back-wave" viewBox="0 0 640 366" preserveAspectRatio="none" aria-hidden="true">
      <path d="M0 366 V338 C230 318 440 268 640 212 V366 Z" fill="var(--brand-blue)"/>
      <path d="M300 305 C440 272 550 238 640 200" fill="none" stroke="var(--brand-grey)" stroke-width="4"/>
    </svg>

    <div class="back-brand">
      <span class="brand-square"></span>
      <span class="brand-name">Tall Fern Roofing</span>
    </div>

    <div class="divider"></div>

    <div class="contact">
      <p class="contact-name">Callum Hartwell</p>
      <p class="contact-title">Managing Director</p>
      <ul class="contact-list">
        <li>
          <svg viewBox="0 0 12 12" aria-hidden="true"><path d="M2.5 1 L4.5 1 L5 3.5 L3.8 4.4 C4.5 6 6 7.5 7.6 8.2 L8.5 7 L11 7.5 L11 9.5 C11 10.3 10.3 11 9.5 11 C5 11 1 7 1 2.5 C1 1.7 1.7 1 2.5 1 Z" fill="var(--brand-blue)"/></svg>
          0400 555 217
        </li>
        <li>
          <svg viewBox="0 0 12 12" aria-hidden="true"><rect x="0.5" y="2" width="11" height="8" fill="var(--brand-blue)"/><path d="M0.5 2 L6 6.5 L11.5 2" fill="none" stroke="#fff" stroke-width="1"/></svg>
          info@tallfernroofing.com
        </li>
        <li>
          <svg viewBox="0 0 12 12" aria-hidden="true"><circle cx="6" cy="6" r="5.5" fill="var(--brand-blue)"/><path d="M0.5 6 H11.5 M6 0.5 C3.5 3 3.5 9 6 11.5 M6 0.5 C8.5 3 8.5 9 6 11.5" fill="none" stroke="#fff" stroke-width="0.8"/></svg>
          www.tallfernroofing.com
        </li>
      </ul>
      <p class="contact-address">1480 Wattle Grove Road<br>Marlow County 5120</p>
    </div>
  </section>

</main>
</body>
</html>
```